Maplecrest Disability - Social Security Disability Attorneys

Our company is expanding to attract clients nationwide for our social security disability practice. We have a logo, but I am looking for a creative and elegant letterhead that projects an image of being technologically advanced but still professional enough for the legal field. I am looking for the "wow factor" combined with this is still professional enough for a law practice.

Requesting letterhead and business card design
Updates

Had to update and change the logo. The previous logo had a typo. Please send updates with the new logo for consideration. The letterhead and business cards should be professional enough to be used for a law firm. Thanks.

Industry/Entity Type

Law Practice, Law Firm, Healthcare Industry, Government

Colors

Designer to choose colors to be used in the design.

Requirements
Nice to have
• **Please create a vertical design for the business card**

```html
<!DOCTYPE html>
<html lang="en">
<head>
<meta charset="utf-8">
<title>Maplecrest Disability – Business Card</title>
<link href="https://fonts.googleapis.com/css2?family=Didact+Gothic&display=swap" rel="stylesheet">
<style>
  :root {
    --bg: #8c8c8c;
    --paper: #ffffff;
    --orange: #ff8616;
    --orange-soft: #ffb166;
    --blue: #1ea2f2;
    --blue-light: #5cc4f5;
    --navy: #1c3fae;
    --grey-text: #6e6e6e;
    --ink: #333333;
    --icon-grey: #7a9ba6;
  }
  * { margin: 0; padding: 0; box-sizing: border-box; }
  html, body { width: 1200px; height: 914px; overflow: hidden; }
  body {
    background: var(--bg);
    font-family: "Didact Gothic", "Century Gothic", sans-serif;
    display: flex;
    align-items: center;
    justify-content: center;
    gap: 70px;
  }
  .card {
    width: 360px;
    height: 630px;
    position: relative;
    overflow: hidden;
    box-shadow: 0 14px 30px rgba(0,0,0,.28);
  }

  /* Front */
  .card-front { background: var(--paper); }
  .corner-tab {
    position: absolute; top: 0; right: 34px;
    width: 30px; height: 14px;
    background: linear-gradient(90deg, var(--orange) 50%, var(--blue) 50%);
  }
  .brand {
    position: absolute; left: 0; right: 0;
    display: flex; align-items: center; justify-content: center; gap: 10px;
    color: var(--navy);
    font-size: 25px; letter-spacing: 2px; text-transform: uppercase;
  }
  .brand-dot { width: 12px; height: 12px; border-radius: 50%; background: var(--orange); flex: none; }
  .card-front .brand { top: 70px; }
  .person { position: absolute; left: 40px; top: 170px; }
  .person-name { color: var(--orange); font-size: 30px; }
  .person-role { color: var(--grey-text); font-size: 17px; margin-top: 2px; }

  .contact-list { position: absolute; left: 0; top: 300px; list-style: none; }
  .contact-item { display: flex; align-items: center; height: 38px; }
  .contact-icon {
    width: 58px; height: 30px; margin-right: 14px;
    display: flex; align-items: center; justify-content: flex-end; padding-right: 8px;
    background: var(--icon-grey);
  }
  .contact-item:first-child .contact-icon { background: var(--blue); height: 36px; }
  .contact-text { font-size: 14px; color: var(--ink); line-height: 1.25; }
  .contact-text.accent { color: var(--orange); font-weight: bold; }
  .front-band {
    position: absolute; left: -40px; bottom: 60px;
    width: 200px; height: 22px;
    background: linear-gradient(90deg, var(--orange), var(--orange-soft));
    transform: rotate(-28deg);
    transform-origin: left center;
  }

  /* Back */
  .card-back {
    background: linear-gradient(180deg, var(--orange) 0%, var(--orange-soft) 32%, #c8c4b4 52%, var(--blue-light) 70%, var(--blue) 100%);
  }
  .card-back .brand { top: 250px; font-size: 24px; }
  .web {
    position: absolute; left: 0; right: 0; bottom: 80px;
    text-align: center; color: #fff; font-size: 19px;
  }
  .bottom-tab {
    position: absolute; bottom: 0; left: 50%; transform: translateX(-50%);
    width: 30px; height: 14px;
    background: linear-gradient(90deg, var(--orange) 50%, var(--blue) 50%);
  }
</style>
</head>
<body>

  <section class="card card-front" aria-label="Business card front">
    <div class="corner-tab"></div>
    <div class="brand"><span class="brand-dot"></span>Maplecrest Disability</div>
    <div class="person">
      <p class="person-name">Example Name</p>
      <p class="person-role">Designation</p>
    </div>
    <ul class="contact-list">
      <li class="contact-item">
        <span class="contact-icon">
          <svg width="14" height="16" viewBox="0 0 14 16"><path d="M7 1a5 5 0 0 0-5 5c0 4 5 9 5 9s5-5 5-9a5 5 0 0 0-5-5z" fill="#fff"/><circle cx="7" cy="6" r="2" fill="#1ea2f2"/></svg>
        </span>
        <span class="contact-text accent">Level 00, 00 Example Street,<br>Example 000 US</span>
      </li>
      <li class="contact-item">
        <span class="contact-icon">
          <svg width="14" height="14" viewBox="0 0 14 14"><path d="M3 1l3 3-2 2c1 2 2 3 4 4l2-2 3 3-2 2C6 13 1 8 1 3z" fill="#fff"/></svg>
        </span>
        <span class="contact-text">0000 000 129</span>
      </li>
      <li class="contact-item">
        <span class="contact-icon">
          <svg width="16" height="12" viewBox="0 0 16 12"><rect x="1" y="1" width="14" height="10" fill="none" stroke="#fff" stroke-width="1.5"/><path d="M1 1l7 6 7-6" fill="none" stroke="#fff" stroke-width="1.5"/></svg>
        </span>
        <span class="contact-text">contact@maplecrestdisability.com</span>
      </li>
      <li class="contact-item">
        <span class="contact-icon">
          <svg width="14" height="14" viewBox="0 0 14 14"><circle cx="7" cy="7" r="6" fill="none" stroke="#fff" stroke-width="1.4"/><path d="M1 7h12M7 1c3 3 3 9 0 12M7 1c-3 3-3 9 0 12" fill="none" stroke="#fff" stroke-width="1.2"/></svg>
        </span>
        <span class="contact-text">www.maplecrestdisability.com</span>
      </li>
    </ul>
    <div class="front-band"></div>
  </section>

  <section class="card card-back" aria-label="Business card back">
    <div class="brand"><span class="brand-dot"></span>Maplecrest Disability</div>
    <p class="web">www.maplecrestdisability.com</p>
    <div class="bottom-tab"></div>
  </section>

</body>
</html>
```